A clean crisp business card for a Landscape Construction company. Designed to be easy to read contact/ info and also be appealing/interesting, unlike a traditional business card.

Industry/Entity Type

Landscape Construction

Contact Information for Business Card

Company name : Brambleford Landscape Construction, phone number: (877) 62Vista, website:Bramblefordyards.example, Email, sales@bramblefordyards.example

Requirements
Nice to have
• Luxurious finishes/ details…. Icons or emblems next to contact info
Should not have
• Clipart or general pictures

```html
<!DOCTYPE html>
<html lang="en">
<head>
<meta charset="utf-8">
<title>Brambleford Landscape Construction – Business Card</title>
<link rel="stylesheet" href="https://fonts.googleapis.com/css2?family=Cinzel:wght@600&family=Didact+Gothic&display=swap">
<style>
  :root {
    --stage: #0b0b0b;
    --card: #141414;
    --edge-green: #9ad21f;
    --brand-blue: #1f73d1;
    --brand-green: #8cc63f;
    --text-light: #d6d6d6;
    --divider: #4a4a4a;
    --emboss: #2a2a2a;
  }
  * { box-sizing: border-box; margin: 0; padding: 0; }
  html, body {
    width: 1200px; height: 820px; overflow: hidden;
    background: var(--stage);
  }
  .stage {
    position: relative; width: 1200px; height: 820px;
    display: flex; align-items: center; justify-content: center; gap: 40px;
  }
  .card {
    position: relative; width: 540px; height: 310px;
    background: var(--card);
    border-left: 2px solid var(--edge-green);
    border-bottom: 2px solid var(--edge-green);
    overflow: hidden;
  }
  /* Front: contact side */
  .brand-column {
    position: absolute; left: 0; top: 0; width: 170px; height: 100%;
    display: flex; align-items: center; justify-content: center;
  }
  .brand-name {
    transform: rotate(-90deg);
    white-space: nowrap; text-align: center;
    font-family: "Didact Gothic", sans-serif; font-weight: 400;
    color: var(--text-light); font-size: 17px; line-height: 1.4;
  }
  .divider {
    position: absolute; left: 180px; top: 40px; bottom: 40px;
    width: 1px; background: var(--divider);
  }
  .contact-block {
    position: absolute; left: 210px; top: 62px; right: 24px;
    font-family: "Didact Gothic", sans-serif; color: var(--text-light);
  }
  .person-name {
    font-family: "Cinzel", serif; font-weight: 600; font-size: 24px;
    letter-spacing: 0.5px; line-height: 1;
  }
  .person-name .first { color: var(--brand-blue); }
  .person-name .last { color: var(--brand-green); }
  .person-role { font-size: 15px; margin-top: 6px; }
  .address { font-size: 14px; line-height: 1.35; margin-top: 22px; }
  .contact-list { list-style: none; margin-top: 20px; font-size: 14px; }
  .contact-list li { display: flex; align-items: center; gap: 10px; margin-bottom: 5px; }
  .contact-list svg { width: 14px; height: 14px; flex: none; }
  /* Back: brand side */
  .card-back .back-lockup {
    position: absolute; right: 34px; bottom: 54px;
    display: flex; align-items: center; gap: 16px;
  }
  .back-circle {
    width: 120px; height: 120px; border-radius: 50%;
    background: radial-gradient(circle at 35% 35%, #3a3a3a, var(--emboss));
  }
  .back-name {
    font-family: "Didact Gothic", sans-serif; font-weight: 400;
    color: var(--text-light); font-size: 20px; line-height: 1.35;
  }
</style>
</head>
<body>
<main class="stage">
  <section class="card card-front" aria-label="Card front with contact details">
    <div class="brand-column">
      <span class="brand-name">Brambleford<br>Landscape Construction</span>
    </div>
    <span class="divider"></span>
    <div class="contact-block">
      <h1 class="person-name"><span class="first">Marcus</span> <span class="last">Hale</span></h1>
      <p class="person-role">Managing Director</p>
      <p class="address">421, Address line Address<br>here 45452, Country Name</p>
      <ul class="contact-list">
        <li>
          <svg viewBox="0 0 16 16" aria-hidden="true"><path fill="var(--brand-green)" d="M3.5 1.5l2.5 3-1.5 1.5c.8 1.9 2.3 3.4 4.2 4.2L10.2 8.7l3 2.5-1.5 2.6C6.6 13.6 2.4 9.4 1 4.3z"/></svg>
          <span>(877) 62Vista</span>
        </li>
        <li>
          <svg viewBox="0 0 16 16" aria-hidden="true"><rect x="1" y="3" width="14" height="10" fill="var(--brand-green)"/><path d="M1 3l7 6 7-6" fill="none" stroke="var(--card)" stroke-width="1.4"/></svg>
          <span>sales@bramblefordyards.example</span>
        </li>
        <li>
          <svg viewBox="0 0 16 16" aria-hidden="true"><g fill="none" stroke="var(--brand-green)" stroke-width="1.4"><circle cx="8" cy="8" r="6.5"/><ellipse cx="8" cy="8" rx="3" ry="6.5"/><path d="M1.5 8h13"/></g></svg>
          <span>www.Bramblefordyards.example</span>
        </li>
      </ul>
    </div>
  </section>

  <section class="card card-back" aria-label="Card back with company name">
    <div class="back-lockup">
      <span class="back-circle"></span>
      <span class="back-name">Brambleford<br>Landscape Construction</span>
    </div>
  </section>
</main>
</body>
</html>
```